BVM Marketing Postcard

Design a 2 Sided marketing postcard for our Real estate management caompany. Looking for a professional yet fresh look that will be printed on a 6"x9" glossy flier

Contact information is www.brixleymanagement.example brixleymanagement@postwellmail.example and 555-014-7283

WE are targeting small condo and town home properties to take on their administrative responsibilities of management

```html
<!DOCTYPE html>
<html lang="en">
<head>
<meta charset="utf-8">
<title>BVM Marketing Postcard</title>
<link rel="stylesheet" href="https://fonts.googleapis.com/css2?family=Montserrat:wght@500;600;700;800&display=swap">
<style>
  :root {
    --navy: #1e2f5c;
    --slate: #4a5a7e;
    --white: #ffffff;
    --page: #ffffff;
    --shadow: rgba(0, 0, 0, 0.45);
  }
  * { margin: 0; padding: 0; box-sizing: border-box; }
  html, body { width: 1200px; height: 1200px; overflow: hidden; background: var(--page); }
  body { position: relative; font-family: "Montserrat", Arial, sans-serif; }

  .postcard {
    position: absolute;
    left: 212px;
    width: 776px;
    height: 524px;
    background: var(--white);
    box-shadow: 6px 6px 8px var(--shadow);
    overflow: hidden;
  }
  .postcard--dark { top: 40px; }
  .postcard--light { top: 635px; }

  .masthead {
    position: absolute; left: 0; top: 0; width: 100%; height: 74px;
    display: flex; flex-direction: column; align-items: center; justify-content: center;
    background: var(--navy); color: var(--white);
  }
  .postcard--light .masthead { background: var(--white); color: var(--slate); height: 76px; }
  .brand-name { font-weight: 700; font-size: 26px; letter-spacing: 0.5px; line-height: 1; }
  .brand-sub { font-weight: 700; font-size: 10px; margin-top: 7px; letter-spacing: 0.2px; }

  .masthead-rule { position: absolute; left: 0; top: 74px; width: 100%; height: 4px; background: var(--white); }

  .panel-who {
    position: absolute; left: 0; top: 77px; width: 388px; height: 392px;
    background: var(--slate); color: var(--white);
    padding: 19px 16px 0 27px;
  }
  .postcard--light .panel-who { top: 76px; height: 395px; }

  .panel-what {
    position: absolute; left: 388px; top: 77px; width: 388px; height: 392px;
    background: var(--white); color: var(--navy);
    padding: 19px 25px 0 14px;
  }
  .postcard--light .panel-what { top: 76px; height: 395px; border-top: 2px solid var(--navy); }

  .section-tag {
    display: inline-block;
    border: 2px solid var(--white);
    font-weight: 800; font-size: 13.5px; letter-spacing: 0.3px;
    padding: 7px 6px 7px 7px;
    line-height: 1;
  }
  .panel-what .section-tag { border-color: var(--navy); }

  .copy { font-weight: 500; font-size: 13.1px; line-height: 15.4px; }
  .copy p { margin-top: 15.4px; text-align: justify; hyphens: manual; }
  .copy p:first-child { margin-top: 0; }
  .panel-who .copy { margin-top: 21px; }
  .panel-who .copy + .section-tag { margin-top: 16px; }
  .panel-who .copy--why { margin-top: 24px; }
  .panel-what .copy { margin-top: 31px; }

  .contact-bar {
    position: absolute; left: 0; bottom: 0; width: 100%; height: 55px;
    background: var(--navy); color: var(--white);
    display: flex; align-items: center; justify-content: center; gap: 12px;
    font-weight: 600; font-size: 14px;
  }
  .contact-bar .divider { font-weight: 500; }
</style>
</head>
<body>

<section class="postcard postcard--dark" aria-label="Postcard, navy header version">
  <header class="masthead">
    <div class="brand-name">BRIXLEY</div>
    <div class="brand-sub">PROPERTY MANAGEMENT</div>
  </header>
  <div class="masthead-rule"></div>

  <div class="panel-who">
    <div class="section-tag">WHO WE ARE</div>
    <div class="copy">
      <p>A professional services organization with a focus on small (3-10 unit) residential buildings.</p>
      <p>Over 30 years of combined experience in real estate and property management.</p>
      <p>Professional, courteous, timely service that is tech&shy;nologically driven.</p>
    </div>
    <div class="section-tag">WHY USE BVM?</div>
    <div class="copy copy--why">
      <p>Owners are rarely suited to manage associations and the burden often falls unfairly on one or two individuals to do all the work.</p>
      <p>Low monthly fees tailored to your needs.</p>
      <p>The Association’s board of directors maintains con&shy;trol of all decision making.</p>
    </div>
  </div>

  <div class="panel-what">
    <div class="section-tag">WHAT WE DO</div>
    <div class="copy">
      <p>Remove the administrative burden of managing small residential buildings</p>
      <p>Utilize economies of scale to reduce expense for all owners across a wide variety of services.</p>
      <p>Collect all assessments and pay all bills</p>
      <p>Provide access to BVM’s client portal with central repository of all association materials (bye-laws, financials, meeting minutes, communications etc)</p>
      <p>Issue 1099 to all contractors as required by law</p>
      <p>Prepare year-end financial statements</p>
      <p>Lender and Legal HOA documents for mortgage companies and sales.</p>
    </div>
  </div>

  <footer class="contact-bar">
    <span>www.brixleymanagement.example</span><span class="divider">|</span>
    <span>brixleymanagement@postwellmail.example</span><span class="divider">|</span>
    <span>555-014-7283</span>
  </footer>
</section>

<section class="postcard postcard--light" aria-label="Postcard, white header version">
  <header class="masthead">
    <div class="brand-name">BRIXLEY</div>
    <div class="brand-sub">PROPERTY MANAGEMENT</div>
  </header>

  <div class="panel-who">
    <div class="section-tag">WHO WE ARE</div>
    <div class="copy">
      <p>A professional services organization with a focus on small (3-10 unit) residential buildings.</p>
      <p>Over 30 years of combined experience in real estate and property management.</p>
      <p>Professional, courteous, timely service that is tech&shy;nologically driven.</p>
    </div>
    <div class="section-tag">WHY USE BVM?</div>
    <div class="copy copy--why">
      <p>Owners are rarely suited to manage associations and the burden often falls unfairly on one or two individuals to do all the work.</p>
      <p>Low monthly fees tailored to your needs.</p>
      <p>The Association’s board of directors maintains con&shy;trol of all decision making.</p>
    </div>
  </div>

  <div class="panel-what">
    <div class="section-tag">WHAT WE DO</div>
    <div class="copy">
      <p>Remove the administrative burden of managing small residential buildings</p>
      <p>Utilize economies of scale to reduce expense for all owners across a wide variety of services.</p>
      <p>Collect all assessments and pay all bills</p>
      <p>Provide access to BVM’s client portal with central repository of all association materials (bye-laws, financials, meeting minutes, communications etc)</p>
      <p>Issue 1099 to all contractors as required by law</p>
      <p>Prepare year-end financial statements</p>
      <p>Lender and Legal HOA documents for mortgage companies and sales.</p>
    </div>
  </div>

  <footer class="contact-bar">
    <span>www.brixleymanagement.example</span><span class="divider">|</span>
    <span>brixleymanagement@postwellmail.example</span><span class="divider">|</span>
    <span>555-014-7283</span>
  </footer>
</section>

</body>
</html>
```